New web design for a service provider in the medical field

We are looking for a new design for our website. We are a company that repairs and sells medical endoscopes. Our customers include doctors and hospitals. Our current website can be found at https://lumavex.de/en/lumavex-english.
We need a new web design (without programming) for the following 3 pages:
-Startpage https://lumavex.de/en/lumavex-english/
-Used endoscopes https://lumavex.de/en/used-endoscopes/
-Purchase https://lumavex.de/en/purchase/
The design should be modern and stylish.
The blue color of the logo should be reflected on the page, but not too intrusive.
I have uploaded the images from the header. If more images are needed, let me know and I will upload them.

Target Market(s)
Doctors and hospitals

```html
<!DOCTYPE html>
<html lang="en">
<head>
<meta charset="utf-8">
<title>Lumavex – Endoscope Repair</title>
<link href="https://fonts.googleapis.com/css2?family=Poppins:wght@300;400;500;600;700;800&family=Roboto+Condensed:wght@400;500;700&display=swap" rel="stylesheet">
<style>
:root{
  --blue:#2b8fd9;
  --blue-dark:#1458b0;
  --navy:#1c3f8c;
  --red:#d3211f;
  --ink:#111;
  --grey-bg:#eceff2;
  --light-blue:#c6dbf1;
  --white:#fff;
}
*{margin:0;padding:0;box-sizing:border-box}
html,body{width:1200px;height:4320px;overflow:hidden}
body{font-family:'Poppins',sans-serif;color:var(--ink);background:var(--white);position:relative}
.abs{position:absolute}
.btn{position:absolute;display:flex;align-items:center;justify-content:center;background:var(--blue);color:#fff;border-radius:30px;font-weight:400;box-shadow:0 4px 10px rgba(0,0,0,.18);white-space:nowrap}
/* header */
.topbar{position:absolute;left:0;top:0;width:1200px;height:94px;background:#fff}
.brand{position:absolute;left:110px;top:28px;display:flex;align-items:center;gap:10px;font-size:24px;font-weight:600;color:var(--blue-dark)}
.brand i{width:14px;height:14px;border-radius:50%;background:var(--blue)}
.tagline{position:absolute;left:377px;top:33px;font-size:17px}
.pill{position:absolute;top:23px;height:46px;background:#1a2433;color:#fff;border-radius:24px;display:flex;align-items:center;gap:12px;padding:0 18px;font-size:15px;white-space:nowrap}
.nav{position:absolute;left:0;top:94px;width:1200px;height:60px;background:var(--blue-dark);display:flex;align-items:center;padding-left:105px;color:#fff;font-size:15.5px;white-space:nowrap}
.nav span{padding:0 16px;border-left:2px solid #fff;line-height:20px}
.nav span:first-child{border-left:none;padding-left:0}
/* hero */
.hero{position:absolute;left:0;top:154px;width:1200px;height:624px;background:var(--grey-bg)}
.hero h1{position:absolute;left:97px;top:150px;font-size:53px;line-height:64px;font-weight:800;letter-spacing:1px}
/* about */
.about-text{position:absolute;left:649px;top:842px;width:450px}
.eyebrow{font-size:25px;font-weight:400}
.sec-title{font-size:24px;font-weight:700;line-height:38px;letter-spacing:.5px}
.body-copy{font-size:15px;line-height:26px;color:#333}
/* brands */
.brands{position:absolute;left:0;top:1452px;width:1200px;height:690px;background:var(--grey-bg)}
.brand-tab{position:absolute;top:67px;height:57px;width:190px;border-radius:30px;color:#fff;font-family:'Roboto Condensed',sans-serif;font-weight:700;font-size:22px;display:flex;align-items:center;justify-content:center}
.card{position:absolute;top:157px;width:308px;height:436px;color:#fff;font-family:'Roboto Condensed',sans-serif}
.card .photo{height:189px}
.card h3{font-size:28px;font-weight:500;margin:16px 0 0 23px}
.card h4{font-size:22px;font-weight:500;margin:10px 0 0 23px}
.card p{font-family:'Poppins',sans-serif;font-size:16px;line-height:27px;margin:8px 18px 0 23px;height:81px;overflow:hidden}
.card .ghost{position:absolute;left:18px;bottom:18px;height:46px;border:2px solid #fff;border-radius:24px;padding:0 16px;display:flex;align-items:center;font-size:19px;font-weight:500;white-space:nowrap}
/* banner */
.banner{position:absolute;left:0;top:2777px;width:1200px;height:332px;background:linear-gradient(90deg,#1b5eaa,#2a78c4 60%,#3d8ccd);color:#fff;text-align:center}
/* features */
.feat-title{position:absolute;left:0;top:3190px;width:1200px;text-align:center;font-size:24px;font-weight:600;letter-spacing:.5px}
.feature{position:absolute;width:230px;font-family:'Roboto Condensed',sans-serif}
.feature h5{font-size:16px;font-weight:500;margin-bottom:8px;white-space:nowrap}
.feature p{font-size:12px;font-weight:500;line-height:17px}
.feature .meta{font-size:12px;margin-top:14px;display:flex;gap:40px;color:#444;white-space:nowrap}
.feature .meta b{color:var(--blue-dark);font-weight:700}
.ficon{position:absolute;width:56px;height:56px;border-radius:50%;background:var(--blue-dark);display:flex;align-items:center;justify-content:center}
.dash{position:absolute;width:0;border-left:2px dashed #777}
/* footer */
.footer{position:absolute;left:0;top:3790px;width:1200px;height:530px;background:#000;color:#fff}
.flinks{position:absolute;top:227px;left:0;width:1200px;display:flex;justify-content:center;gap:26px;font-size:16px;font-weight:500}
.fcircle{position:absolute;width:60px;height:60px;border-radius:50%;background:var(--blue-dark);display:flex;align-items:center;justify-content:center}
.ftext{position:absolute;font-size:15px;line-height:25px;font-weight:500;white-space:nowrap}
</style>
</head>
<body>

<header>
  <div class="topbar">
    <div class="brand"><i></i>Lumavex</div>
    <div class="tagline">Cause the outcome matters</div>
    <div class="pill" style="left:655px;width:232px">
      <svg width="20" height="16" viewBox="0 0 20 16"><rect x="1" y="1" width="18" height="14" rx="2" fill="none" stroke="#fff" stroke-width="2"/><path d="M1 2l9 7 9-7" fill="none" stroke="#fff" stroke-width="2"/></svg>
      info@lumavex.de</div>
    <div class="pill" style="left:902px;width:200px">
      <svg width="18" height="18" viewBox="0 0 24 24"><path fill="#fff" d="M6.6 10.8a15 15 0 006.6 6.6l2.2-2.2c.3-.3.7-.4 1-.2 1.1.4 2.3.6 3.6.6.6 0 1 .4 1 1V20c0 .6-.4 1-1 1A17 17 0 013 4c0-.6.4-1 1-1h3.5c.6 0 1 .4 1 1 0 1.3.2 2.5.6 3.6.1.3 0 .7-.2 1z"/></svg>
      <span style="font-size:14.5px">+49 6532 555 017-0</span></div>
  </div>
  <nav class="nav">
    <span>HOME</span><span>ENDOSCOPE REPAIR</span><span>USED ENDOSCOPES</span><span>ENDOSCOPY SYSTEMS</span><span>ENDOSCOPY ACCESSORIES</span><span>PURCHASE</span>
  </nav>
</header>

<section class="hero">
  <h1>PUT YOUR<br>ENDOSCOPE IN<br>RELIABLE HANDS!</h1>
  <div class="btn" style="left:99px;top:379px;width:200px;height:49px;font-size:21px">Get Started</div>
  <svg class="abs" style="left:0;top:0" width="1200" height="624" role="img" aria-label="Photo of a smiling doctor wearing a head lamp and holding an endoscope">
    <defs><linearGradient id="heroPhoto" x1="0" y1="0" x2="1" y2="1"><stop offset="0" stop-color="#dfe6ee"/><stop offset=".5" stop-color="#c9d3de"/><stop offset="1" stop-color="#9fb0c2"/></linearGradient></defs>
    <path d="M770 0 L1200 0 L1200 470 Q1140 610 960 616 Q790 620 660 460 Q580 350 650 240 Z" fill="url(#heroPhoto)"/>
    <path d="M640 450 Q780 625 960 620 Q1130 612 1200 470" fill="none" stroke="var(--blue)" stroke-width="5"/>
  </svg>
</section>

<section class="about">
  <svg class="abs" style="left:0;top:778px" width="600" height="570" role="img" aria-label="Photo of a doctor examining a young woman's nose with a flexible endoscope">
    <defs><linearGradient id="aboutPhoto" x1="0" y1="0" x2="1" y2="1"><stop offset="0" stop-color="#d7dde4"/><stop offset=".6" stop-color="#a9b9cc"/><stop offset="1" stop-color="#7f96b3"/></linearGradient></defs>
    <path d="M0 0 L400 0 L560 160 Q610 230 560 330 Q470 520 340 560 Q180 570 0 400 Z" fill="url(#aboutPhoto)"/>
    <path d="M0 400 Q180 570 340 560" fill="none" stroke="var(--blue)" stroke-width="5"/>
  </svg>
  <div class="about-text">
    <div class="eyebrow">ABOUT US</div>
    <div class="sec-title">WE ARE YOUR EXPERTS FOR<br>REPAIRING FLEXIBLE ENDOSCOPES</div>
    <p class="body-copy" style="margin-top:14px">Lumavex GmbH is specialized in repairing and saling flexible endoscopes along with accessories and consumables. We offer endoscopes, processors, light sources, accessories and much more – with a focus on the manufacturers Orvana, Penlux and Fujora.</p>
    <p class="body-copy" style="margin-top:26px">We applied for foundation in 2020, whereby Lumavex emerged from another company in the same business field. For this reason, all employees have many years of experience. Lumavex is a reliable contact for doctors and hospitals.</p>
  </div>
  <div class="btn" style="left:644px;top:1279px;width:201px;height:48px;font-size:21px">Learn More</div>
</section>

<section class="brands">
  <div class="brand-tab" style="left:297px;background:var(--navy)">ORVANA</div>
  <div class="brand-tab" style="left:505px;background:var(--red)">PENLUX</div>
  <div class="brand-tab" style="left:713px;background:#000">FUJORA</div>

  <article class="card" style="left:100px;background:var(--navy)">
    <div class="photo" role="img" aria-label="Photo of a technician repairing an endoscope control body" style="background:linear-gradient(135deg,#cfd6dc,#6f8596)"></div>
    <h3>REPAIR</h3><h4>ENDOSCOPE REPAIR SERVICE</h4>
    <p>Manufacturer-independent we repair and maintain endoscopes, individual components (e.g.</p>
    <div class="ghost">Repair request</div>
  </article>
  <article class="card" style="left:446px;background:var(--red)">
    <div class="photo" role="img" aria-label="Photo of a gloved hand placing instruments into a cleaning tray" style="background:linear-gradient(135deg,#b8bec4,#565f68)"></div>
    <h3>SALE</h3><h4>USED ENDOSCOPES</h4>
    <p>Our regular stock includes refurbished gastroscopes, coloscopes, bronchoscopes,</p>
    <div class="ghost">Purchase request</div>
  </article>
  <article class="card" style="left:790px;background:#000">
    <div class="photo" role="img" aria-label="Photo of surgeons in blue gowns handling an endoscope" style="background:linear-gradient(135deg,#4b7fd6,#1d3f8f)"></div>
    <h3>PURCHASE</h3><h4>USED ENDOSCOPES</h4>
    <p>We are very interested in buying your old endoscopes – even defective and dismantled! We</p>
    <div class="ghost">Sell device</div>
  </article>
</section>

<section class="endoscope">
  <div class="abs" style="left:97px;top:2228px;width:470px">
    <div class="eyebrow">Endoscope</div>
    <div class="sec-title" style="font-size:25px;line-height:37px;margin-top:10px">ENDOSCOPE REPAIRS AND SECOND HAND ENDOSCOPES FROM LUMAVEX – CAUSE THE OUTCOME MATTERS!</div>
    <p class="body-copy" style="margin-top:22px;width:455px">Lumavex is a privileged partner for the start-up facility or optimisation of existing healthcare facilities, doctor's offices and hospitals. The quality and reliability of our products and our offered service are our best advertisement!</p>
  </div>
  <div class="btn" style="left:95px;top:2606px;width:202px;height:50px;font-size:21px">Learn More</div>
  <svg class="abs" style="left:600px;top:2142px" width="600" height="550" role="img" aria-label="Close-up photo of an endoscope control handle with angulation knobs">
    <defs><linearGradient id="scopePhoto" x1="0" y1="0" x2="1" y2="1"><stop offset="0" stop-color="#e4eaf0"/><stop offset=".5" stop-color="#9aa8b6"/><stop offset="1" stop-color="#3a4654"/></linearGradient></defs>
    <path d="M180 0 L600 0 L600 300 Q520 470 370 535 Q220 560 90 440 Q0 340 40 200 Q70 110 180 0 Z" fill="url(#scopePhoto)"/>
    <path d="M240 548 Q400 550 600 300" fill="none" stroke="var(--blue)" stroke-width="6"/>
  </svg>
</section>

<section class="banner" role="img" aria-label="Blue tinted photo of an endoscopy workplace">
  <div style="position:absolute;top:58px;width:1200px;font-size:25px;font-weight:700;letter-spacing:.5px">FAULTY ENDOSCOPE?</div>
  <div style="position:absolute;top:98px;width:1200px;font-size:27px;font-weight:300">We ensure quick and smooth repairs!</div>
  <div style="position:absolute;top:148px;width:1200px;font-size:24px;font-weight:700;letter-spacing:1px">SIMPLE PLACE A</div>
  <div class="btn" style="left:501px;top:220px;width:200px;height:45px;font-size:21px;background:#2e92df;box-shadow:none">Pick-up order</div>
</section>

<section class="features">
  <div class="feat-title">LUMAVEX GMBH, YOUR DECISION FOR YOUR FUTURE</div>
  <div class="abs" style="left:436px;top:3260px;width:327px;height:176px;background:var(--light-blue)"></div>

  <div class="dash" style="left:142px;top:3320px;height:160px"></div>
  <div class="dash" style="left:481px;top:3320px;height:160px"></div>
  <div class="dash" style="left:818px;top:3320px;height:160px"></div>

  <div class="ficon" style="left:114px;top:3270px"><svg width="28" height="28" viewBox="0 0 24 24"><circle cx="12" cy="7" r="4" fill="none" stroke="#fff" stroke-width="2"/><path d="M4 22c0-5 4-8 8-8s8 3 8 8" fill="none" stroke="#fff" stroke-width="2"/></svg></div>
  <div class="ficon" style="left:453px;top:3270px"><svg width="28" height="28" viewBox="0 0 24 24"><circle cx="12" cy="9" r="6" fill="none" stroke="#fff" stroke-width="2"/><path d="M8 14l-2 8 6-3 6 3-2-8" fill="none" stroke="#fff" stroke-width="2"/></svg></div>
  <div class="ficon" style="left:790px;top:3270px"><svg width="28" height="28" viewBox="0 0 24 24"><path d="M6 3v7a4 4 0 008 0V3M10 14v3a4 4 0 008 0v-3" fill="none" stroke="#fff" stroke-width="2"/><circle cx="18" cy="12" r="2" fill="#fff"/></svg></div>
  <div class="ficon" style="left:114px;top:3485px"><svg width="28" height="28" viewBox="0 0 24 24"><circle cx="12" cy="7" r="4" fill="none" stroke="#fff" stroke-width="2"/><path d="M4 22c0-5 4-8 8-8s8 3 8 8M12 14v8" fill="none" stroke="#fff" stroke-width="2"/></svg></div>
  <div class="ficon" style="left:453px;top:3485px"><svg width="28" height="28" viewBox="0 0 24 24"><circle cx="12" cy="8" r="4" fill="none" stroke="#fff" stroke-width="2"/><path d="M4 22c0-5 4-8 8-8s8 3 8 8" fill="none" stroke="#fff" stroke-width="2"/><path d="M9 18h6" stroke="#fff" stroke-width="2"/></svg></div>
  <div class="ficon" style="left:790px;top:3485px"><svg width="28" height="28" viewBox="0 0 24 24"><circle cx="12" cy="7" r="4" fill="none" stroke="#fff" stroke-width="2"/><path d="M4 22c0-5 4-8 8-8s8 3 8 8M9 17l2 2 4-4" fill="none" stroke="#fff" stroke-width="2"/></svg></div>

  <div class="feature" style="left:189px;top:3278px"><h5>Fast repairs</h5><p>Keep potential disruptions in your doctor's office or in your hospital at minimum as a result of optimized processes and highly qualified specialists in our company</p><div class="meta"><span>Magna aliqua.</span><b>Learn More →</b></div></div>
  <div class="feature" style="left:528px;top:3278px;color:#fff"><h5>On-site service</h5><p>We will gladly pay you a visit to to carry out analysis and repairs on site. Due to our many years of experience – it doesn't get any faster (within a 250 km range)</p><div class="meta" style="color:#fff"><span>Magna aliqua.</span><b style="color:#fff">Learn More →</b></div></div>
  <div class="feature" style="left:865px;top:3278px"><h5>Without a maintenance contract</h5><p>No subscription or other maintenance contract, but one-time and sustainable repair work</p><div class="meta" style="margin-top:31px"><span>Magna aliqua.</span><b>Learn More →</b></div></div>
  <div class="feature" style="left:189px;top:3494px"><h5>Highly cost efficient</h5><p>Benefit from our first class recommendations and implementation by our experienced staff. Our goals is to find the best solutions together with you at the</p><div class="meta"><span>Magna aliqua.</span><b>Learn More →</b></div></div>
  <div class="feature" style="left:528px;top:3494px"><h5>Loan equipment service</h5><p>Use our service of high-quality loan devices during the downtime of your defective endoscope (limited to stock)</p><div class="meta" style="margin-top:31px"><span>Magna aliqua.</span><b>Learn More →</b></div></div>
  <div class="feature" style="left:865px;top:3494px"><h5>First class service</h5><p>Our clients always come first!</p><div class="meta" style="margin-top:65px"><span>Magna aliqua.</span><b>Learn More →</b></div></div>

  <div class="btn" style="left:466px;top:3651px;width:268px;height:38px;font-size:14px">Learn more about Lumavex!</div>
</section>

<footer class="footer">
  <div style="position:absolute;top:75px;width:1200px;text-align:center;font-size:34px;font-weight:600">Lumavex</div>
  <div class="flinks"><span>INFORMATIONS</span><span>ABOUT US</span><span>CONTACT US</span><span>TOS</span><span>COPYRIGHTS</span><span>PRIVACY POLICY</span></div>

  <div class="fcircle" style="left:164px;top:300px"><svg width="24" height="30" viewBox="0 0 24 30"><path d="M12 1a10 10 0 0110 10c0 8-10 18-10 18S2 19 2 11A10 10 0 0112 1z" fill="#fff"/><circle cx="12" cy="11" r="4" fill="var(--blue-dark)"/></svg></div>
  <div class="ftext" style="left:248px;top:316px">Lindenweg 12<br>56789 Falkenau<br>Germany</div>
  <div class="abs" style="left:474px;top:295px;width:2px;height:62px;background:#fff"></div>

  <div class="fcircle" style="left:508px;top:300px"><svg width="26" height="26" viewBox="0 0 24 24"><path fill="#fff" d="M6.6 10.8a15 15 0 006.6 6.6l2.2-2.2c.3-.3.7-.4 1-.2 1.1.4 2.3.6 3.6.6.6 0 1 .4 1 1V20c0 .6-.4 1-1 1A17 17 0 013 4c0-.6.4-1 1-1h3.5c.6 0 1 .4 1 1 0 1.3.2 2.5.6 3.6.1.3 0 .7-.2 1z"/></svg></div>
  <div class="ftext" style="left:592px;top:303px">Phone<br>+49 6532 555 017-0</div>
  <div class="abs" style="left:759px;top:295px;width:2px;height:62px;background:#fff"></div>

  <div class="fcircle" style="left:791px;top:300px"><svg width="28" height="22" viewBox="0 0 20 16"><rect x="1" y="1" width="18" height="14" rx="2" fill="none" stroke="#fff" stroke-width="1.6"/><path d="M1 2l9 7 9-7" fill="none" stroke="#fff" stroke-width="1.6"/></svg></div>
  <div class="ftext" style="left:878px;top:300px">info@lumavex.de</div>

  <div class="abs" style="left:114px;top:405px;width:975px;border-top:1px dashed #aaa"></div>
  <div style="position:absolute;top:437px;width:1200px;text-align:center;font-size:15px">© Copyright 2022 Lumavex , All Rights Reserved.</div>
</footer>

</body>
</html>
```